Valentines Day Helicopter Tour Mailer

The purpose behind this project is to design a mailer for helicopter tours around valentines day. Not sure exaclty all what to include as i'm not sure if i want to price on it yet but i want helicopters, hearts, and something interesting to draw attention to the service we will be offering. If we did include price it would be $169/ person. Size should be good for 8.5 by 11 paper

general public

```html
<!DOCTYPE html>
<html lang="en">
<head>
<meta charset="utf-8">
<title>Valentine's Day Helicopter Tours Mailer</title>
<link href="https://fonts.googleapis.com/css2?family=Oswald:wght@500;600&family=Allura&family=Marcellus&display=swap" rel="stylesheet">
<style>
  :root {
    --backdrop: #9c258e;
    --ink: #0b0b0c;
    --pink: #ec0b8c;
    --plum: #9b2590;
    --white: #ffffff;
    --forest: #24372a;
    --forest-light: #3d5a3c;
    --stone: #8a8b8c;
    --machine: #121314;
  }
  * { box-sizing: border-box; margin: 0; padding: 0; }
  html, body { width: 1015px; height: 1200px; overflow: hidden; }
  body { background: var(--backdrop); position: relative; font-family: "Oswald", sans-serif; }

  .mailer {
    position: absolute; left: 133px; top: 117px; width: 748px; height: 943px;
    background: var(--ink); overflow: hidden;
  }
  .scene-photo {
    position: absolute; inset: 0;
    background:
      linear-gradient(180deg, rgba(11,11,12,0.85) 0%, rgba(11,11,12,0.15) 16%, rgba(11,11,12,0) 40%, rgba(11,11,12,0) 66%, rgba(11,11,12,0.7) 84%, var(--ink) 100%),
      radial-gradient(ellipse 190px 260px at 60px 500px, var(--machine) 0%, rgba(18,19,20,0.92) 55%, rgba(18,19,20,0) 100%),
      radial-gradient(ellipse 260px 110px at 470px 740px, rgba(200,200,202,0.75) 0%, rgba(160,160,162,0.35) 60%, rgba(160,160,162,0) 100%),
      radial-gradient(ellipse 260px 200px at 640px 470px, var(--forest-light) 0%, rgba(36,55,42,0) 100%),
      linear-gradient(160deg, #6b6d6e 0%, #4a4d4d 18%, var(--forest) 34%, #2c4631 52%, #4e605c 62%, var(--stone) 72%, #5a5b5c 84%, #222223 100%);
  }

  .brand {
    position: absolute; left: 0; right: 0; top: 74px;
    display: flex; align-items: center; justify-content: center; gap: 12px;
  }
  .brand-dot { width: 16px; height: 16px; border-radius: 50%; background: var(--pink); }
  .brand-name {
    font-family: "Oswald", sans-serif; font-weight: 600; font-size: 40px;
    color: var(--white); letter-spacing: 1px; line-height: 1;
  }

  .hearts { position: absolute; left: 0; top: 0; width: 1015px; height: 1200px; }

  .offer {
    position: absolute; left: 355px; width: 270px; text-align: center;
    color: var(--white); text-transform: uppercase; font-weight: 500;
  }
  .offer-headline { top: 611px; font-size: 21px; line-height: 29px; }
  .offer-headline .pill {
    display: inline-block; background: var(--pink); border-radius: 14px;
    padding: 0 14px; line-height: 25px; margin: 2px 0;
  }
  .offer-sub { top: 711px; font-size: 15px; line-height: 18px; }

  .title {
    position: absolute; left: 133px; width: 748px; top: 826px; text-align: center;
    font-family: "Allura", cursive; font-weight: 400; font-size: 112px; color: var(--pink); line-height: 1;
  }
  .occasion {
    position: absolute; left: 133px; width: 748px; top: 956px; text-align: center;
    font-family: "Marcellus", serif; font-size: 31px; line-height: 38px; color: var(--white); letter-spacing: 0.5px;
  }
  .price {
    position: absolute; left: 375px; top: 1004px; width: 265px; height: 29px;
    background: var(--pink); border-radius: 15px; text-align: center;
    font-family: "Marcellus", serif; font-size: 24px; line-height: 29px;
    color: var(--white); letter-spacing: 2px;
  }
</style>
</head>
<body>
  <main class="mailer">
    <div class="scene-photo" role="img" aria-label="Black helicopter parked on a rocky riverbank with forested mountains and a river behind"></div>
    <div class="brand">
      <span class="brand-dot"></span>
      <span class="brand-name">Skyward Helicopters</span>
    </div>
  </main>

  <svg class="hearts" viewBox="0 0 1015 1200">
    <defs>
      <linearGradient id="coupleFill" x1="0" y1="0" x2="0" y2="1">
        <stop offset="0" stop-color="#2e3f31"/>
        <stop offset="0.35" stop-color="#5b4a55"/>
        <stop offset="0.55" stop-color="#b86a9a"/>
        <stop offset="0.75" stop-color="#d5348f"/>
        <stop offset="1" stop-color="#a10f69"/>
      </linearGradient>
      <path id="smallHeart" d="M0 -6 C-6 -16 -22 -14 -22 0 C-22 12 -8 20 0 28 C8 20 22 12 22 0 C22 -14 6 -16 0 -6 Z"/>
    </defs>
    <path role="img" aria-label="Couple in wedding attire embracing beside the helicopter"
          d="M530 452 C470 370 280 370 278 510 C276 640 400 740 448 824 C560 775 730 690 742 560 C752 430 620 400 530 452 Z"
          fill="url(#coupleFill)" stroke="#ec0b8c" stroke-width="22" stroke-linejoin="round"/>
    <use href="#smallHeart" transform="translate(383 452) scale(0.9)" fill="#9b2590"/>
    <use href="#smallHeart" transform="translate(413 424) scale(0.45)" fill="#ec0b8c"/>
    <use href="#smallHeart" transform="translate(597 410) scale(0.6)" fill="#9b2590"/>
    <use href="#smallHeart" transform="translate(656 398) scale(1.35)" fill="#ec0b8c"/>
    <use href="#smallHeart" transform="translate(709 648) scale(2.65) rotate(8)" fill="#9b2590"/>
  </svg>

  <div class="offer offer-headline">
    The only<br><span class="pill">Valentine’s Day</span><br>Surprise, you’ll need
  </div>
  <div class="offer offer-sub">Enjoy the ride<br>with your valentine</div>

  <h1 class="title">Helicopter Tours</h1>
  <p class="occasion">AROUND VALENTINES DAY</p>
  <p class="price">$169 PER PERSON</p>
</body>
</html>
```